Book Cover for Lantern Cousins Notes from the Orchard

We have written a book that brings together Notes from the Orchard from a variety of women's voices.
We developed a draft book cover that we like using Canva (attached below). We'd love a book cover that is similar to this image, but looks more professional.
Following are the themes we’d like to depict in the book cover, and in parentheses, how they are represented in the current cover:
1. Divinely feminine (overall cover)
2. Currents of enlightenment (the swirls of light carrying the butterfly)
3. Diversity (a myriad of colors)
4. The solo journey into the unknown (the single butterfly’s flight)
5. Buoyancy and joy (again, the dancing colors and floating butterfly)
6. Boldly feminine (the blue butterfly, set against brush strokes of light)
7. Homage to a dear friend (she loved blue butterflies, the cosmos - this butterfly has hints of the cosmos in her wings, and painting - this background has brush strokes of light).
Book Title, Subtitle, and Editor:
Lantern Cousins
Notes from the Orchard
Edited by Ilse Varno
Thank you very much for considering this project!
People who are interested in Women and Spirituality

```html
<!DOCTYPE html>
<html lang="en">
<head>
<meta charset="utf-8">
<title>Lantern Cousins — Notes from the Orchard</title>
<link rel="stylesheet" href="https://fonts.googleapis.com/css2?family=Cinzel:wght@400;500;600&family=Great+Vibes&display=swap">
<style>
  :root {
    --navy: #0c1482;
    --title-blue: #0a89c7;
    --wash-pink: #f7b8ef;
    --wash-cream: #fdf7ee;
    --wash-lilac: #c9b7f3;
    --wash-sky: #bfeefd;
    --wash-periwinkle: #8ea4ee;
    --wash-lemon: #f7f3b6;
    --wing-deep: #0f2fb8;
    --wing-bright: #19bfee;
  }
  * { margin: 0; padding: 0; box-sizing: border-box; }
  html, body { width: 752px; height: 1200px; overflow: hidden; background: #fff; }

  .cover {
    position: relative;
    width: 752px;
    height: 1200px;
    overflow: hidden;
    font-family: "Cinzel", "Times New Roman", serif;
  }

  .watercolor-wash {
    position: absolute;
    inset: 0;
    background:
      radial-gradient(ellipse 260px 160px at 660px 30px, var(--wash-pink), transparent 70%),
      radial-gradient(ellipse 200px 140px at 60px 210px, rgba(247,184,239,.7), transparent 70%),
      radial-gradient(ellipse 180px 80px at 150px 510px, rgba(142,164,238,.75), transparent 70%),
      radial-gradient(ellipse 140px 80px at 170px 520px, rgba(247,150,230,.6), transparent 70%),
      radial-gradient(ellipse 260px 200px at 120px 700px, rgba(201,183,243,.8), transparent 70%),
      radial-gradient(ellipse 300px 120px at 200px 860px, rgba(247,243,182,.6), transparent 70%),
      radial-gradient(ellipse 420px 180px at 330px 960px, rgba(150,232,252,.8), transparent 70%),
      radial-gradient(ellipse 260px 120px at 140px 1080px, rgba(142,164,238,.8), transparent 70%),
      radial-gradient(ellipse 200px 90px at 120px 1140px, rgba(247,160,230,.7), transparent 70%),
      radial-gradient(ellipse 240px 140px at 640px 1060px, rgba(247,243,182,.55), transparent 70%),
      radial-gradient(ellipse 220px 240px at 720px 640px, rgba(247,184,239,.55), transparent 70%),
      linear-gradient(180deg, var(--wash-cream) 0%, #fdeefc 40%, #f3f0fd 70%, #eefbff 100%);
  }

  .editor-line {
    position: absolute;
    top: 46px;
    left: 0;
    width: 752px;
    text-align: center;
    color: var(--navy);
    font-size: 31px;
    font-weight: 600;
    letter-spacing: 0.36em;
    padding-left: 0.36em;
  }

  .series-name {
    position: absolute;
    top: 90px;
    left: 0;
    width: 752px;
    text-align: center;
    color: var(--navy);
    font-size: 48px;
    font-weight: 500;
    letter-spacing: 0.32em;
    padding-left: 0.32em;
  }

  .book-title {
    position: absolute;
    top: 252px;
    left: 0;
    width: 752px;
    text-align: center;
    color: var(--title-blue);
    font-weight: 400;
  }
  .book-title .line {
    display: block;
    white-space: nowrap;
  }
  .book-title .line-one {
    font-size: 86px;
    letter-spacing: 0.22em;
    line-height: 100px;
  }
  .book-title .line-two {
    margin-top: 10px;
    font-size: 70px;
    letter-spacing: 0.14em;
    padding-left: 0.14em;
    line-height: 90px;
  }
  .book-title .connector {
    font-family: "Great Vibes", cursive;
    font-size: 86px;
    letter-spacing: 0;
    margin-left: -6px;
  }

  .butterfly-art {
    position: absolute;
    left: 288px;
    top: 500px;
    width: 302px;
    height: 420px;
    border-radius: 60% 40% 50% 50% / 55% 45% 55% 45%;
    background:
      radial-gradient(ellipse 80px 70px at 200px 150px, var(--wing-bright), transparent 75%),
      radial-gradient(ellipse 110px 90px at 130px 270px, var(--wing-bright), transparent 75%),
      radial-gradient(ellipse 160px 220px at 55% 50%, var(--wing-deep), transparent 90%);
    opacity: 0.9;
  }
</style>
</head>
<body>
  <main class="cover">
    <div class="watercolor-wash" role="img" aria-label="Soft watercolour wash of pink, lilac, sky blue and pale yellow brush strokes of light"></div>

    <p class="editor-line">EDITED BY ILSE VARNO</p>
    <p class="series-name">LANTERN COUSINS</p>

    <h1 class="book-title">
      <span class="line line-one">NOTES<span class="connector">from</span></span>
      <span class="line line-two">THE ORCHARD</span>
    </h1>

    <div class="butterfly-art" role="img" aria-label="Glowing blue butterfly with star-speckled wings floating on currents of light"></div>
  </main>
</body>
</html>
```